New National Dermatology Group needs a business card!

We need a business card for our new national company that has 3 brands within the business:
Lumora Clinics Australia, Tessaly Clinics Australia and Corvane Clinics Australia.
We help people access dermatology services close to home throughout Australia.
We need a business card that has:
all 3 logos on it,
Our websites (there are three, listed above)
Our email (there are three, listed above)
The location of our first clinic: 41 Willow Rd Parramatta (this can then be changed for each location as required)

```html
<!DOCTYPE html>
<html lang="en">
<head>
<meta charset="utf-8">
<title>Dermatology Group Business Card</title>
<link href="https://fonts.googleapis.com/css2?family=Roboto:wght@400;500&family=Roboto+Condensed:wght@700&family=Cormorant+Garamond:ital@1&display=swap" rel="stylesheet">
<style>
  :root {
    --bg: #2a2a2c;
    --paper: #fbfbf9;
    --green: #2aa64a;
    --orange: #f08a24;
    --brown: #7a3f1c;
    --ink: #3a3a3a;
  }
  * { margin: 0; padding: 0; box-sizing: border-box; }
  html, body { width: 1200px; height: 874px; overflow: hidden; background: var(--bg); }
  .canvas { position: relative; width: 1200px; height: 874px; }

  .card {
    position: absolute;
    background: var(--paper);
    border-radius: 18px;
    overflow: hidden;
    box-shadow: 0 6px 18px rgba(0,0,0,.35);
  }

  /* Brand name: one colour, one weight, plain dot beside */
  .brand-name { display: flex; align-items: center; gap: 8px;
    font-family: "Roboto", sans-serif; font-weight: 500; line-height: 1.2; }
  .brand-name .dot { flex: none; width: 10px; height: 10px; border-radius: 50%; background: currentColor; }
  .lumora { color: var(--green); }
  .tessaly { color: var(--orange); }
  .corvane { color: var(--brown); }

  /* Front: three brands stacked */
  .card-front { left: 135px; top: 167px; width: 310px; height: 540px;
    display: flex; flex-direction: column; align-items: center; justify-content: center; gap: 30px; }
  .brand { display: flex; flex-direction: column; align-items: center; }
  .card-front .brand-name { font-size: 21px; }
  .brand-url { font-family: "Roboto Condensed", sans-serif; font-weight: 700; font-size: 11.5px;
    color: #2b2b2b; margin-top: 10px; letter-spacing: .2px; }
  .divider { width: 22px; height: 2px; background: var(--green); }

  /* Back: contact side */
  .card-back { left: 505px; top: 277px; width: 560px; height: 320px; }
  .card-back .band { position: absolute; inset: 0; width: 560px; height: 320px; }
  .person { position: absolute; left: 58px; top: 160px; transform: translate(-50%, -50%) rotate(-90deg);
    text-align: center; color: #fff; white-space: nowrap; }
  .person-name { font-family: "Roboto", sans-serif; font-weight: 400; font-size: 20px; letter-spacing: 2px; text-transform: uppercase; }
  .person-role { font-family: "Cormorant Garamond", serif; font-style: italic; font-size: 15px; margin-top: 2px; }

  .contacts { position: absolute; left: 168px; top: 18px; }
  .contact-block { margin-bottom: 12px; }
  .contact-line { display: flex; align-items: center; gap: 7px; font-family: "Roboto", sans-serif;
    font-size: 11.5px; color: var(--ink); line-height: 15px; }
  .contact-line .ico { width: 10px; height: 10px; flex: none; }
  .contact-line.indent { padding-left: 17px; }
  .block-lumora .ico { fill: var(--green); }
  .block-tessaly .ico { fill: var(--orange); }
  .block-corvane .ico { fill: var(--brown); }

  .brands-column { position: absolute; left: 400px; top: 0; bottom: 0; width: 145px;
    display: flex; flex-direction: column; justify-content: center; gap: 40px; }
  .brands-column .brand-name { font-size: 16px; align-items: flex-start; }
  .brands-column .brand-name .dot { margin-top: 5px; }
</style>
</head>
<body>
<svg width="0" height="0" style="position:absolute">
  <symbol id="i-pin" viewBox="0 0 10 10"><path d="M5 0a3.6 3.6 0 0 0-3.6 3.6C1.4 6.3 5 10 5 10s3.6-3.7 3.6-6.4A3.6 3.6 0 0 0 5 0zm0 5a1.4 1.4 0 1 1 0-2.8A1.4 1.4 0 0 1 5 5z"/></symbol>
  <symbol id="i-phone" viewBox="0 0 10 10"><path d="M2 .5l1.6 2.2-.9 1.1c.6 1.2 1.3 1.9 2.5 2.5l1.1-.9L8.5 7 7.7 9C4 8.7 1.3 6 1 2.3z"/></symbol>
  <symbol id="i-mail" viewBox="0 0 10 10"><path d="M0 2h10v6H0zM.8 2.6 5 5.6l4.2-3V2.4H.8z"/></symbol>
  <symbol id="i-web" viewBox="0 0 10 10"><path d="M5 0a5 5 0 1 0 0 10A5 5 0 0 0 5 0zm0 1.2a3.8 3.8 0 1 1 0 7.6 3.8 3.8 0 0 1 0-7.6zM3.2 4.3h3.6v1.4H3.2z"/></symbol>
</svg>

<main class="canvas">
  <section class="card card-front">
    <div class="brand">
      <div class="brand-name lumora"><span class="dot"></span>Lumora Clinics Australia</div>
      <div class="brand-url">LUMORACLINICSAUSTRALIA.COM.AU</div>
    </div>
    <div class="divider"></div>
    <div class="brand">
      <div class="brand-name tessaly"><span class="dot"></span>Tessaly Clinics Australia</div>
      <div class="brand-url">WWW.TESSALYCLINICS.COM.AU</div>
    </div>
    <div class="divider"></div>
    <div class="brand">
      <div class="brand-name corvane"><span class="dot"></span>Corvane Clinics Australia</div>
      <div class="brand-url">WWW.CORVANECLINICS.COM.AU</div>
    </div>
  </section>

  <section class="card card-back">
    <svg class="band" viewBox="0 0 560 320" aria-hidden="true">
      <path d="M0 0H150C95 80 120 230 62 320H0Z" fill="var(--green)"/>
      <path d="M160 0C105 80 130 230 72 320" fill="none" stroke="var(--orange)" stroke-width="6"/>
      <path d="M172 0C117 80 142 230 84 320" fill="none" stroke="var(--brown)" stroke-width="3"/>
    </svg>
    <div class="person">
      <div class="person-name">Daniel Reyes</div>
      <div class="person-role">President</div>
    </div>

    <div class="contacts">
      <div class="contact-block block-lumora">
        <div class="contact-line"><svg class="ico"><use href="#i-pin"/></svg>41 Willow Rd</div>
        <div class="contact-line indent">Parramatta, NSW 2150</div>
        <div class="contact-line"><svg class="ico"><use href="#i-phone"/></svg>02-5550-1947</div>
        <div class="contact-line"><svg class="ico"><use href="#i-mail"/></svg>info@lumoraclinicsaustralia.com.au</div>
        <div class="contact-line"><svg class="ico"><use href="#i-web"/></svg>lumoraclinicsaustralia.com.au</div>
      </div>
      <div class="contact-block block-tessaly">
        <div class="contact-line"><svg class="ico"><use href="#i-pin"/></svg>41 Willow Rd</div>
        <div class="contact-line indent">Parramatta, NSW 2150</div>
        <div class="contact-line"><svg class="ico"><use href="#i-phone"/></svg>02-5550-1947</div>
        <div class="contact-line"><svg class="ico"><use href="#i-mail"/></svg>info@tessalyclinics.com.au</div>
        <div class="contact-line"><svg class="ico"><use href="#i-web"/></svg>tessalyclinics.com.au</div>
      </div>
      <div class="contact-block block-corvane">
        <div class="contact-line"><svg class="ico"><use href="#i-pin"/></svg>41 Willow Rd</div>
        <div class="contact-line indent">Parramatta, NSW 2150</div>
        <div class="contact-line"><svg class="ico"><use href="#i-phone"/></svg>02-5550-1947</div>
        <div class="contact-line"><svg class="ico"><use href="#i-mail"/></svg>info@corvaneclinics.com.au</div>
        <div class="contact-line"><svg class="ico"><use href="#i-web"/></svg>corvaneclinics.com.au</div>
      </div>
    </div>

    <div class="brands-column">
      <div class="brand-name lumora"><span class="dot"></span>Lumora Clinics Australia</div>
      <div class="brand-name tessaly"><span class="dot"></span>Tessaly Clinics Australia</div>
      <div class="brand-name corvane"><span class="dot"></span>Corvane Clinics Australia</div>
    </div>
  </section>
</main>
</body>
</html>
```